Design NEW business card

We would like a business card using the colour deep red wine or dark navy blue textured background (patterned or not, open to suggestions) with a high gloss debossed rose gold/copper RM Roland Mercer Jewellery business name (Provided). I have included images for your review we would like to keep our currently logo and business name on the front but you can change the layout and positioning. For the back of the card we are open to all suggestions/variations.
Business
Use our current RM Roland Mercer Jewellery logo (Provided image)

```html
<!DOCTYPE html>
<html lang="en">
<head>
<meta charset="utf-8">
<title>Roland Mercer Jewellery – Business Card</title>
<link href="https://fonts.googleapis.com/css2?family=Montserrat:wght@400;500&display=swap" rel="stylesheet">
<style>
  :root {
    --backdrop: #e6e3de;
    --card-navy: #141b2e;
    --card-navy-deep: #0d1221;
    --card-light: #f5f4f2;
    --pattern-tone: #dcdad6;
    --pattern-soft: #ebe9e6;
    --rose-gold: #c7936a;
    --ink: #1c1c1c;
    --shadow: rgba(0, 0, 0, 0.22);
  }
  * { margin: 0; padding: 0; box-sizing: border-box; }
  html, body {
    width: 1200px;
    height: 900px;
    overflow: hidden;
    background: var(--backdrop);
    font-family: "Montserrat", sans-serif;
  }
  .canvas {
    position: relative;
    width: 1200px;
    height: 900px;
  }
  .card {
    position: absolute;
    left: 250px;
    width: 700px;
    height: 400px;
    box-shadow: 0 10px 28px var(--shadow);
    overflow: hidden;
  }
  .card--front {
    top: 35px;
    background: radial-gradient(ellipse at 50% 45%, var(--card-navy), var(--card-navy-deep));
  }
  .card--back { top: 465px; background: var(--card-light); }

  .brand {
    position: absolute;
    inset: 0;
    display: flex;
    align-items: center;
    justify-content: center;
    gap: 22px;
    color: var(--rose-gold);
  }
  .brand__dot {
    width: 54px;
    height: 54px;
    border-radius: 50%;
    background: var(--rose-gold);
  }
  .brand__name {
    font-weight: 500;
    font-size: 30px;
    letter-spacing: 0.22em;
    line-height: 1.4;
    text-transform: uppercase;
  }
  .brand__name span { display: block; font-size: 14px; letter-spacing: 0.6em; }

  .card__pattern {
    position: absolute;
    inset: 0;
    background:
      radial-gradient(circle at 50% 50%, var(--card-light) 0%, var(--pattern-soft) 55%, var(--pattern-tone) 100%);
  }
  .contact {
    position: absolute;
    inset: 0;
    text-align: center;
    color: var(--ink);
    padding-top: 70px;
  }
  .contact__name { font-size: 24px; font-weight: 400; letter-spacing: 0.04em; }
  .contact__role { font-size: 14px; letter-spacing: 0.06em; margin-top: 2px; }
  .contact__details { font-size: 17px; line-height: 1.45; margin-top: 52px; letter-spacing: 0.04em; }
  .contact__web { font-size: 17px; margin-top: 30px; letter-spacing: 0.08em; }
</style>
</head>
<body>
<main class="canvas">
  <section class="card card--front" aria-label="Card front">
    <div class="brand">
      <div class="brand__dot"></div>
      <div class="brand__name">Roland Mercer<span>Jewellery</span></div>
    </div>
  </section>

  <section class="card card--back" aria-label="Card back">
    <div class="card__pattern" role="img" aria-label="Blind-embossed repeating pattern of overlapping circles, white on white, covering the whole card"></div>
    <div class="contact">
      <p class="contact__name">DANIEL HART</p>
      <p class="contact__role">CEO/FOUNDER</p>
      <p class="contact__details">
        2140 Willow Crest Road, Juneau, Alaska 34512<br>
        P: 555 210 3847 M: 555 318 6620 F: 555 402 7715<br>
        E: hello@rolandmercer.com
      </p>
      <p class="contact__web">www.rolandmercer.com</p>
    </div>
  </section>
</main>
</body>
</html>
```